New Business Card Design Project

Use the flyer uploaded and website www.brightoakbuilders.com for inspiration.
List Our Services on Backside of business cards
Marcus Delling
Harborline Builders Inc.
Licensed General Contractors
858-471-6093

Contact Information for Business Card

Use the flyer uploaded and website www.brightoakbuilders.com for inspiration. List Our Services on Backside of business cards Marcus Delling Harborline Builders Inc. Licensed General Contractors 858-471-6093

```html
<!DOCTYPE html>
<html lang="en">
<head>
<meta charset="utf-8">
<title>Harborline Builders – Business Card</title>
<link href="https://fonts.googleapis.com/css2?family=Montserrat:wght@400;500;700&display=swap" rel="stylesheet">
<style>
  :root {
    --backdrop: #e9e6e1;
    --card-light: #ffffff;
    --card-dark: #222222;
    --ink: #111111;
    --ink-soft: #1c1c1c;
    --paper-text: #f2f2f2;
  }
  * { margin: 0; padding: 0; box-sizing: border-box; }
  html, body {
    width: 900px; height: 1200px; overflow: hidden;
    background: var(--backdrop);
    font-family: "Montserrat", Arial, sans-serif;
  }
  .canvas { position: relative; width: 900px; height: 1200px; }
  .card {
    position: absolute; width: 743px; height: 440px; border-radius: 24px;
    box-shadow: 0 6px 18px rgba(0,0,0,0.25);
  }
  .card--front { left: 80px; top: 131px; background: var(--card-light); color: var(--ink); }
  .card--back { left: 79px; top: 639px; background: var(--card-dark); color: var(--paper-text); }

  .brand {
    position: absolute; left: 40px; width: 350px; text-align: center;
    font-weight: 500; font-size: 24px; letter-spacing: 1px; text-transform: uppercase;
  }
  .card--front .brand { top: 266px; color: var(--ink); }
  .card--back .brand { top: 272px; color: var(--paper-text); }

  .person { position: absolute; left: 398px; top: 144px; }
  .person__name { font-size: 27px; font-weight: 700; line-height: 32px; }
  .person__role { font-size: 15px; font-weight: 500; line-height: 20px; }

  .contacts { position: absolute; left: 398px; top: 222px; list-style: none; }
  .contacts li {
    display: flex; align-items: center; height: 28px;
    font-size: 15.5px; font-weight: 500;
  }
  .contacts svg { width: 17px; height: 17px; margin-right: 15px; fill: var(--ink-soft); }

  .license { position: absolute; left: 399px; top: 323px; font-size: 15.5px; font-weight: 500; }

  .services { position: absolute; left: 395px; top: 112px; }
  .services__title {
    display: inline-block; font-size: 20px; font-weight: 700; line-height: 26px;
    padding-bottom: 4px; border-bottom: 1.5px solid var(--paper-text); padding-right: 4px;
  }
  .services__list { list-style: none; margin-top: 10px; }
  .services__list li {
    position: relative; padding-left: 20px; font-size: 15.5px; line-height: 24.2px;
  }
  .services__list li::before {
    content: ""; position: absolute; left: 3px; top: 10px;
    width: 6px; height: 6px; border-radius: 50%; background: var(--paper-text);
  }
</style>
</head>
<body>
<main class="canvas">
  <section class="card card--front">
    <div class="brand">Harborline Builders</div>

    <div class="person">
      <p class="person__name">Marcus Delling</p>
      <p class="person__role">Managing Director</p>
    </div>

    <ul class="contacts">
      <li>
        <svg viewBox="0 0 24 24" aria-hidden="true"><path d="M3 8c0-2 2-4 9-4s9 2 9 4v2h-5V8H8v2H3zM6 11h12l2 9H4zm6 2a3 3 0 1 0 0 6 3 3 0 0 0 0-6z"/></svg>
        858-471-6093
      </li>
      <li>
        <svg viewBox="0 0 24 24" aria-hidden="true"><path d="M2 5h20v2l-10 6L2 7zm0 4l10 6 10-6v10H2z"/></svg>
        info@brightoakbuilders.com
      </li>
      <li>
        <svg viewBox="0 0 24 24" aria-hidden="true"><path d="M12 2a10 10 0 1 0 0 20 10 10 0 0 0 0-20zm-1 3c-2 1-4 3-4 5 2 0 3 1 3 3s2 2 2 4v3a8 8 0 0 1-7-7c0-4 3-7 6-8zm4 1a8 8 0 0 1 4 9c-1-1-2-2-4-2-1-2 1-3 0-5z"/></svg>
        www.brightoakbuilders.com
      </li>
    </ul>

    <p class="license">CSLB Licensed No. #2047518</p>
  </section>

  <section class="card card--back">
    <div class="brand">Harborline Builders</div>

    <div class="services">
      <h2 class="services__title">Our Services</h2>
      <ul class="services__list">
        <li>Remodel: Kitchen &amp; Bath</li>
        <li>Painting: Interior &amp; Exterior</li>
        <li>Flooring: Carpet, Vinyl, Wood</li>
        <li>Window: Door Replacement</li>
        <li>Plumbing: Repair &amp; Upgrades</li>
        <li>Energy Efficienct Upgrades</li>
        <li>Deck &amp; Patio consturction</li>
        <li>Water &amp; Mold Damage</li>
        <li>Garage Renovation</li>
      </ul>
    </div>
  </section>
</main>
</body>
</html>
```